Business Card Design For A Cajun Seafood Restaurant

We are opening a cajun seafood restaurant in a week. We mainly serve cajun seafood which is orginally from Louisiana. We want design on both sides of a business card. I have menu on the website. You can go to www.reednkettle.example to check out our menu.

Restaurant name: Reed N' Kettle
Phone: +1 (555) 304-7712
Address: 48206 Ludlow Row, #7, Bexmoor Flats, Ca90000
Email: reednkettle@mailbox.example
Website: www.reednkettle.example

Maybe add social media icons (facebook, instagram) if looks nice on the business card.
facebook.com/reednkettle
instagram.com/reednkettle or @reednkettle

Attached is the logo and other business card samples that I like.

```html
<!DOCTYPE html>
<html lang="en">
<head>
<meta charset="utf-8">
<title>Reed N' Kettle — Business Card</title>
<link href="https://fonts.googleapis.com/css2?family=Open+Sans:wght@400;600;800&display=swap" rel="stylesheet">
<style>
  :root {
    --stage: #3b3b3b;
    --card: #f7f7f7;
    --ink-black: #0d0d0d;
    --brand-orange: #f36a10;
    --brand-yellow: #fcc20a;
    --text-grey: #4f4f4f;
    --rule-grey: #8a8a8a;
    --crab-orange: #ef7424;
    --corn-yellow: #f7c948;
  }
  * { margin: 0; padding: 0; box-sizing: border-box; }
  html, body { width: 1200px; height: 750px; overflow: hidden; }
  body {
    background: var(--stage);
    font-family: "Open Sans", sans-serif;
    position: relative;
  }
  .card {
    position: absolute;
    top: 228px;
    width: 460px;
    height: 262px;
    border-radius: 14px;
    background: var(--card);
    overflow: hidden;
  }
  .card--front { left: 124px; }
  .card--back { left: 618px; }

  .front-waves { position: absolute; inset: 0; width: 100%; height: 100%; }

  .holder { position: absolute; right: 24px; top: 26px; text-align: right; }
  .holder__name { color: var(--brand-orange); font-size: 17px; font-weight: 600; line-height: 1.2; }
  .holder__role { color: #fff; font-size: 13px; line-height: 1.35; }

  .mascot { position: absolute; }
  .mascot--small {
    left: 78px; top: 72px; width: 72px; height: 66px;
    background:
      radial-gradient(ellipse 38% 22% at 52% 20%, var(--corn-yellow), rgba(247,201,72,0) 100%),
      radial-gradient(ellipse 50% 48% at 50% 58%, var(--crab-orange) 40%, rgba(239,116,36,0) 100%);
  }
  .mascot--large {
    left: 206px; top: 10px; width: 256px; height: 252px;
    background:
      radial-gradient(ellipse 30% 20% at 60% 20%, var(--corn-yellow) 30%, rgba(247,201,72,0) 100%),
      radial-gradient(ellipse 46% 44% at 50% 56%, var(--crab-orange) 45%, rgba(239,116,36,0) 100%);
  }

  .wordmark {
    position: absolute;
    display: flex;
    align-items: center;
    gap: 7px;
    color: var(--brand-orange);
    font-weight: 800;
    text-transform: uppercase;
    white-space: nowrap;
  }
  .wordmark__dot { width: 10px; height: 10px; border-radius: 50%; background: var(--brand-orange); }
  .wordmark--front { left: 32px; top: 144px; font-size: 16px; }
  .wordmark--back { left: 26px; top: 180px; font-size: 17px; }

  .contacts { position: absolute; left: 26px; top: 191px; list-style: none; }
  .contacts li {
    display: flex; align-items: center; gap: 7px;
    color: var(--text-grey); font-size: 12.5px; line-height: 17.5px;
  }
  .contacts svg { width: 11px; height: 11px; flex: none; }

  .address {
    position: absolute; right: 24px; top: 209px; text-align: right;
    color: var(--text-grey); font-size: 12.5px; line-height: 17.5px; font-style: normal;
  }

  .social { position: absolute; left: 26px; top: 213px; width: 168px; height: 24px; }
  .social__rule { position: absolute; left: 0; right: 0; top: 12px; height: 1px; background: var(--rule-grey); }
  .social__dot {
    position: absolute; top: 0; width: 24px; height: 24px; border-radius: 50%;
    background: var(--brand-orange); border: 2px solid var(--card);
  }
  .social__dot--one { left: 62px; }
  .social__dot--two { left: 90px; }
</style>
</head>
<body>

<section class="card card--front" aria-label="Business card front">
  <svg class="front-waves" viewBox="0 0 575 328" preserveAspectRatio="none" aria-hidden="true">
    <path fill="var(--ink-black)" d="M0,0 H575 V98 C520,118 430,125 360,95 C280,60 220,30 150,30 C80,30 30,90 0,160 Z"/>
    <path fill="var(--brand-orange)" d="M0,172 C28,92 88,42 160,38 C205,36 240,50 270,74 C232,56 195,48 160,50 C98,56 42,110 0,180 Z"/>
    <path fill="var(--brand-yellow)" d="M355,88 C430,122 515,116 575,70 V92 C520,126 430,132 355,88 Z"/>
  </svg>

  <div class="holder">
    <p class="holder__name">MARLA VOSS</p>
    <p class="holder__role">CEO/Founder</p>
  </div>

  <div class="mascot mascot--small" role="img" aria-label="Illustrated crab mascot holding an ear of corn"></div>

  <div class="wordmark wordmark--front"><span class="wordmark__dot"></span>Reed N' Kettle</div>

  <ul class="contacts">
    <li>
      <svg viewBox="0 0 12 12" aria-hidden="true"><path fill="var(--brand-orange)" d="M2.4,0.6 L4.2,2.8 L3.2,4.2 C3.9,5.8 5.6,7.6 7.6,8.6 L9,7.6 L11.4,9.4 L10.2,11.4 C5.4,11.2 0.8,6.4 0.6,1.8 Z"/></svg>
      +1 (555) 304-7712
    </li>
    <li>
      <svg viewBox="0 0 12 12" aria-hidden="true"><rect x="0.5" y="2" width="11" height="8" fill="var(--brand-orange)"/><path d="M0.8,2.4 L6,6.6 L11.2,2.4" fill="none" stroke="#fff" stroke-width="1"/></svg>
      reednkettle@mailbox.example
    </li>
    <li>
      <svg viewBox="0 0 12 12" aria-hidden="true"><circle cx="6" cy="6" r="5.5" fill="var(--brand-orange)"/><path d="M0.5,6 H11.5 M6,0.5 C3.5,3 3.5,9 6,11.5 M6,0.5 C8.5,3 8.5,9 6,11.5" fill="none" stroke="#fff" stroke-width="0.8"/></svg>
      www.reednkettle.example
    </li>
  </ul>

  <address class="address">
    48206 Ludlow Row, #7<br>
    Bexmoor Flats, Ca90000
  </address>
</section>

<section class="card card--back" aria-label="Business card back">
  <div class="wordmark wordmark--back"><span class="wordmark__dot"></span>Reed N' Kettle</div>

  <div class="social" aria-label="Social media links">
    <span class="social__rule"></span>
    <span class="social__dot social__dot--one"></span>
    <span class="social__dot social__dot--two"></span>
  </div>

  <div class="mascot mascot--large" role="img" aria-label="Large illustrated crab mascot lifting an ear of corn over its head"></div>
</section>

</body>
</html>
```